Design and Renovation Company Luxury Business Card

I want to create a luxury business card for a Design and Renovation Firm . We will use our current logo. The company name is 528BUILDA. We do not want anything standard. We need a very unique concept.
Please see uploaded inspiration. I really like the textured paper option. I would like the card to be thick with debossing, and/or embossing options. The logo has orange in it but I would like to see the card with and without the orange. I think the orange may make the company feel less high-end. The goal is to elevate the logo not match its vibe per se of the logo. We want something very unique, not standard at all!
I would like a space for :
Logo,
Name,
Position,
Email,
Office number,
Website Address,
Business Address,
Thank you!
Have fun!
Target Market(s)
Home owners Age 35 +
Industry/Entity Type
Design and Renovation
Contact Information for Business Card
Logo, Name, Position, Email, Office number, Website Address, Business Address,.
Colors
Designer to choose colors to be used in the design.
Requirements
Must have
- A luxury designer feel. Must be black or dark grey but open to other luxury ideas.
Nice to have
- Gold, silver, black embossing or debossing. Textured paper design.
Should not have
- A cheap look and feel.

```html
<!DOCTYPE html>
<html lang="en">
<head>
<meta charset="utf-8">
<title>528BUILDA Business Card</title>
<link href="https://fonts.googleapis.com/css2?family=Montserrat:wght@400;500;700&display=swap" rel="stylesheet">
<style>
  :root {
    --stage: #2b2b2b;
    --ink: #151515;
    --paper: #ffffff;
    --accent: #f7941d;
    --text-dark: #1b1b1b;
    --text-light: #f2f2f2;
  }
  * { box-sizing: border-box; margin: 0; padding: 0; }
  html, body { width: 1200px; height: 801px; overflow: hidden; }
  body {
    background: var(--stage);
    font-family: "Montserrat", sans-serif;
    display: flex;
    align-items: center;
    justify-content: center;
    gap: 40px;
  }
  .card {
    position: relative;
    width: 520px;
    height: 297px;
    border-bottom: 3px solid var(--accent);
    overflow: hidden;
  }
  .card-front { background: var(--paper); }
  .card-back { background: var(--ink); }

  /* front */
  .front-band { position: absolute; inset: 0; width: 100%; height: 100%; }
  .front-name {
    position: absolute;
    left: 42px;
    top: 126px;
    width: 176px;
    font-weight: 500;
    font-size: 24px;
    letter-spacing: 1px;
    color: var(--text-dark);
    line-height: 1;
  }
  .divider {
    position: absolute;
    left: 236px;
    top: 70px;
    width: 1.5px;
    height: 112px;
    background: var(--accent);
  }
  .contact {
    position: absolute;
    left: 252px;
    top: 66px;
    color: var(--text-dark);
  }
  .person-name { font-size: 20px; font-weight: 700; color: var(--accent); line-height: 1.1; }
  .person-role { font-size: 10.5px; margin-bottom: 8px; }
  .contact-line {
    display: flex;
    align-items: center;
    gap: 8px;
    font-size: 11px;
    line-height: 1.7;
  }
  .contact-line svg { width: 10px; height: 10px; flex: none; }
  .address {
    position: absolute;
    left: 110px;
    right: 30px;
    bottom: 18px;
    text-align: center;
    font-size: 11.5px;
    color: var(--text-light);
    letter-spacing: 0.3px;
  }

  /* back */
  .back-content {
    position: absolute;
    left: 0;
    right: 0;
    top: 50%;
    transform: translateY(-50%);
    text-align: center;
    color: var(--text-light);
  }
  .back-name {
    font-size: 52px;
    font-weight: 500;
    letter-spacing: 3px;
    line-height: 1;
  }
  .back-descriptor {
    font-size: 11px;
    font-weight: 500;
    letter-spacing: 5px;
    margin-top: 22px;
  }
</style>
</head>
<body>

  <section class="card card-front" aria-label="Business card front">
    <svg class="front-band" viewBox="0 0 520 297" preserveAspectRatio="none" aria-hidden="true">
      <polygon points="70,297 92,244 470,244 492,236 520,236 520,297" fill="#151515"/>
    </svg>

    <div class="front-name">528BUILDA</div>

    <div class="divider"></div>

    <div class="contact">
      <div class="person-name">Daniel Moore</div>
      <div class="person-role">Managing Director</div>
      <div class="contact-line">
        <svg viewBox="0 0 10 10"><path d="M2 1 L4 1 L4.6 3 L3.5 4 Q4.5 6 6 6.5 L7 5.4 L9 6 L9 8 Q5 9 2.2 6.5 Q1 4 2 1Z" fill="#f7941d"/></svg>
        <span>555-014-0173</span>
      </div>
      <div class="contact-line">
        <svg viewBox="0 0 10 10"><rect x="0.5" y="2" width="9" height="6.5" fill="#f7941d"/><path d="M0.5 2 L5 5.6 L9.5 2" stroke="#fff" stroke-width="0.9" fill="none"/></svg>
        <span>hello@528builda.com</span>
      </div>
      <div class="contact-line">
        <svg viewBox="0 0 10 10"><circle cx="5" cy="5" r="4.5" fill="#f7941d"/><path d="M0.5 5 H9.5 M5 0.5 Q2.5 5 5 9.5 M5 0.5 Q7.5 5 5 9.5" stroke="#fff" stroke-width="0.7" fill="none"/></svg>
        <span>www.528builda.com</span>
      </div>
    </div>

    <p class="address">415 Elm Grove Ave, #112 Lakeport, OH 43210</p>
  </section>

  <section class="card card-back" aria-label="Business card back">
    <div class="back-content">
      <div class="back-name">528BUILDA</div>
      <div class="back-descriptor">Design and Renovation Firm</div>
    </div>
  </section>

</body>
</html>
```